Stationery Design Project for Nimbora, Chicago

Nimbora, a street parking application which helps car drivers find a street parking spot by offering an ideal path along which to look for parking. This path is calculated by our algorithm based on data (e.g. historical data, baseball games schedule, etc.). Along this path the driver will find a spot and will also save 70% of the search time. Customer we target is reg. between 21 and 45 yo.

We envision something young, fresh, bright and original. Slightly abstract maybe. It should represent the idea and elements of finding street parking in the city, e.g. car(s), parking spot, people, city, etc. (just ideas!).

Logo is attached.

Requirement:
- Business Cards (2 Sided Full Color CMYK)
- Letterhead (1 Sided Full Color CMYK)
- Envelope (1 Sided Full Color CMYK)
- Sticker (1 Sided Full Color CMYK), round with a 2inch diameter.

Reason: We're starting to get more and more designs and need more time to look into all of them. Very exciting!! Thanks to everybody!

Hi all, we're in the process of selecting our favs. Though choices!!! Really good submissions. Will keep you posted and sorry for the delay.

Target Market(s)

Car drivers and owners between 21 and 45

Industry/Entity Type

Parking

Requirements
Must have
• Sticker should be round and include company URL nimbora.com and the new logo which we will attach soon.
Should not have
• Should not be too serious or boring.

```html
<!DOCTYPE html>
<html lang="en">
<head>
<meta charset="utf-8">
<title>Nimbora Business Card</title>
<link rel="stylesheet" href="https://fonts.googleapis.com/css2?family=Open+Sans:wght@400;600;700&display=swap">
<style>
  :root {
    --backdrop: #e9e6e2;
    --card: #ffffff;
    --navy: #2d3385;
    --royal: #2f5fb8;
    --ink: #2e2e30;
    --name: #5a5fa8;
    --muted: #555558;
    --mark: #1f6fd6;
    --street-light: #8c8480;
    --street-dark: #4a4644;
  }
  * { box-sizing: border-box; margin: 0; padding: 0; }
  html, body { width: 1200px; height: 423px; overflow: hidden; }
  body {
    background: var(--backdrop);
    font-family: "Open Sans", Arial, sans-serif;
    position: relative;
  }
  .card {
    position: absolute;
    top: 69px;
    width: 513px;
    height: 294px;
    background: var(--card);
    border-radius: 18px;
    overflow: hidden;
    box-shadow: 0 2px 6px rgba(0,0,0,0.25);
  }
  .card--front { left: 78px; }
  .card--back { left: 629px; }
  .card__band { position: absolute; inset: 0; width: 100%; height: 100%; }

  .brand { position: absolute; display: flex; align-items: center; }
  .brand__dot { border-radius: 50%; background: var(--mark); flex: none; }
  .brand__name {
    font-weight: 600;
    color: var(--ink);
    letter-spacing: 0.5px;
    line-height: 1;
  }
  .card--front .brand { left: 35px; top: 32px; }
  .card--front .brand__dot { width: 86px; height: 86px; margin-right: 18px; }
  .card--front .brand__name { font-size: 54px; }

  .holder { position: absolute; left: 37px; top: 156px; }
  .holder__name { font-size: 17px; font-weight: 700; color: var(--name); }
  .holder__title { font-size: 13px; font-weight: 400; color: var(--name); }
  .address {
    position: absolute; left: 37px; top: 192px;
    font-size: 12px; line-height: 17px; color: var(--ink);
  }

  .contacts {
    position: absolute; right: 24px; top: 192px;
    list-style: none; color: #fff; font-size: 13.5px; text-align: right;
  }
  .contacts li { display: flex; align-items: center; justify-content: flex-end; height: 21.5px; }
  .contacts svg { width: 11px; height: 11px; margin-left: 6px; flex: none; }

  .card--back .brand {
    left: 45px; top: 58px; width: 140px;
    flex-direction: column;
  }
  .card--back .brand__dot { width: 104px; height: 104px; }
  .card--back .brand__name { font-size: 22px; margin-top: 12px; }
  .url {
    position: absolute; left: 52px; top: 234px;
    font-size: 12.5px; letter-spacing: 1.2px; color: var(--muted);
  }
  .street-photo {
    position: absolute; left: 222px; top: 51px; width: 291px; height: 198px;
    background: linear-gradient(180deg, var(--street-light) 0%, var(--street-dark) 35%, #5b5856 60%, var(--street-dark) 78%, #7d7a78 100%);
  }
</style>
</head>
<body>

<section class="card card--front">
  <svg class="card__band" viewBox="0 0 513 294" preserveAspectRatio="none" aria-hidden="true">
    <defs>
      <linearGradient id="band-fill" x1="0" y1="1" x2="1" y2="0">
        <stop offset="0" stop-color="var(--navy)"/>
        <stop offset="1" stop-color="var(--royal)"/>
      </linearGradient>
    </defs>
    <path d="M513 0 L513 294 L0 294 L0 270 Q 380 250 513 0 Z" fill="url(#band-fill)"/>
  </svg>

  <div class="brand">
    <span class="brand__dot"></span>
    <span class="brand__name">nimbora</span>
  </div>

  <p class="holder"><span class="holder__name">Your Name ,</span> <span class="holder__title">Title</span></p>
  <p class="address">Complex Name, Street Name<br>Area, City Name,000 000</p>

  <ul class="contacts">
    <li>+1 312 555 0147
      <svg viewBox="0 0 12 12"><circle cx="6" cy="6" r="6" fill="#fff"/><path d="M3.5 3 L5 3 L5.6 4.6 L4.8 5.2 Q5.6 6.6 6.8 7.2 L7.4 6.4 L9 7 L9 8.5 Q5 8.8 3.5 3 Z" fill="var(--royal)"/></svg>
    </li>
    <li>+1 312 555 0147
      <svg viewBox="0 0 12 12"><rect x="3" y="0.5" width="6" height="11" rx="1" fill="#fff"/><rect x="4" y="2" width="4" height="4" fill="var(--royal)"/></svg>
    </li>
    <li>info@nimbora.com
      <svg viewBox="0 0 12 12"><circle cx="6" cy="6" r="6" fill="#fff"/><rect x="2.8" y="4" width="6.4" height="4.4" fill="var(--royal)"/><path d="M2.8 4 L6 6.5 L9.2 4" stroke="#fff" stroke-width="0.8" fill="none"/></svg>
    </li>
    <li>www.nimbora.com
      <svg viewBox="0 0 12 12"><circle cx="6" cy="6" r="6" fill="#fff"/><path d="M1.5 6 H10.5 M6 1.5 V10.5 M2.5 3.8 H9.5 M2.5 8.2 H9.5" stroke="var(--royal)" stroke-width="0.7"/></svg>
    </li>
  </ul>
</section>

<section class="card card--back">
  <div class="brand">
    <span class="brand__dot"></span>
    <span class="brand__name">nimbora</span>
  </div>
  <p class="url">www.nimbora.com</p>
  <div class="street-photo" role="img" aria-label="Aerial photo of a city street with cars parked along both curbs"></div>
</section>

</body>
</html>
```